Business cards to launch an education platform

Hi,
I am looking at having new business cards designed.
I am a startup, developing a web platform for schools and university, the education world. It's an online assessment system.
I would like a card that looks classy, and that is using the colors and the font of my logo.

I have attached:
1) my logo
2) A business card that I have designed quickly so you can have all the information required in the card, but I really don't like it.
3) The font that I am using (Lato Regular) to design my web platform
4) Some screenshots of my web platform so you can have a look at the style that I have.

Target Market(s)

Major market: Education system: Schools and university
Minor markets: Business in general

Industry/Entity Type

Business

Contact Information for Business Card

Clara Fenwick
Director

M: 0437 518 902
E: clara.fenwick@amberLoomSystems.com.au

Requirements
Must have
• The colors of my logo

```html
<!DOCTYPE html>
<html lang="en">
<head>
<meta charset="utf-8">
<title>Amber Loom Systems – Business Card</title>
<link rel="stylesheet" href="https://fonts.googleapis.com/css2?family=Lato:wght@400;700&display=swap">
<style>
  :root {
    --page-bg: #e6e8eb;
    --navy-deep: #0a1730;
    --navy-mid: #1c3a5e;
    --navy-soft: #2a4f78;
    --frost-light: #f2f3f2;
    --frost-shade: #d9dcda;
    --teal-line: #1f8f9e;
    --name-blue: #3d94d1;
    --title-white: #eef2f7;
    --label-teal: #4fa3c4;
    --number-pink: #f3d6de;
    --email-grey: #c9d2dc;
    --brand-navy: #13304f;
  }
  * { margin: 0; padding: 0; box-sizing: border-box; }
  html, body {
    width: 1200px;
    height: 969px;
    overflow: hidden;
    background: var(--page-bg);
    font-family: "Lato", sans-serif;
  }
  .business-card {
    position: absolute;
    left: 100px;
    top: 200px;
    width: 1000px;
    height: 568px;
    overflow: hidden;
    box-shadow: 0 14px 40px rgba(10, 23, 48, 0.25);
  }
  .card-art {
    position: absolute;
    inset: 0;
    width: 1000px;
    height: 568px;
  }
  .holder-name {
    position: absolute;
    left: 46px;
    top: 44px;
    font-size: 37px;
    font-weight: 400;
    letter-spacing: 0.5px;
    color: var(--name-blue);
    text-transform: uppercase;
  }
  .holder-role {
    position: absolute;
    left: 46px;
    top: 96px;
    font-size: 27px;
    color: var(--title-white);
    text-transform: uppercase;
    letter-spacing: 0.5px;
  }
  .contact-mobile {
    position: absolute;
    left: 46px;
    top: 448px;
    font-size: 27px;
    letter-spacing: 0.5px;
  }
  .contact-label { color: var(--label-teal); }
  .contact-number { color: var(--number-pink); }
  .contact-email {
    position: absolute;
    left: 46px;
    top: 492px;
    font-size: 25px;
    color: var(--email-grey);
  }
  .brand-mark {
    position: absolute;
    left: 690px;
    top: 150px;
    width: 150px;
    height: 150px;
    background: var(--brand-navy);
  }
  .brand-name {
    position: absolute;
    left: 580px;
    top: 318px;
    width: 370px;
    text-align: center;
    font-size: 50px;
    line-height: 1.15;
    font-weight: 400;
    letter-spacing: 3px;
    color: var(--brand-navy);
  }
</style>
</head>
<body>
  <div class="business-card">
    <svg class="card-art" viewBox="0 0 1000 568" xmlns="http://www.w3.org/2000/svg" aria-hidden="true">
      <defs>
        <linearGradient id="frostGradient" x1="0" y1="0" x2="1" y2="1">
          <stop offset="0" stop-color="var(--frost-light)"/>
          <stop offset="0.55" stop-color="var(--frost-shade)"/>
          <stop offset="1" stop-color="var(--frost-light)"/>
        </linearGradient>
        <radialGradient id="navyGlow" cx="0.3" cy="0.45" r="0.75">
          <stop offset="0" stop-color="var(--navy-soft)"/>
          <stop offset="0.6" stop-color="var(--navy-mid)"/>
          <stop offset="1" stop-color="var(--navy-deep)"/>
        </radialGradient>
      </defs>
      <rect class="frost-panel" width="1000" height="568" fill="url(#frostGradient)"/>
      <polygon class="navy-panel" points="0,0 679,0 481,137 481,404 730,568 0,568" fill="url(#navyGlow)"/>
      <polyline class="hex-frame" points="690,0 492,137 492,404 742,568" fill="none" stroke="var(--teal-line)" stroke-width="7"/>
    </svg>

    <div class="holder-name">Clara Fenwick</div>
    <div class="holder-role">Director</div>
    <div class="contact-mobile"><span class="contact-label">Mobile : </span><span class="contact-number">0437 518 902</span></div>
    <div class="contact-email">clara.fenwick@amberLoomSystems.com.au</div>

    <div class="brand-mark"></div>
    <div class="brand-name">AMBER LOOM<br>Systems</div>
  </div>
</body>
</html>
```